professional business card design for technology company

We are a small technology consulting firm, specialising in consulting based around Cloud and Managed services. Our colour scheme is yellow, blue and white, as you can see in the logos. Although we are based in melbourne australia, due to the nature of our work, our clients can be located anywhere. We are looking for a clean, professional, positive look - similar to our company logo

Target Market(s)

small business

Industry/Entity Type

Business

Contact Information for Business Card

eye catching, designed to incorporate some level of raised printing. Must contain website address, phone number, name and job title

Requirements
Must have
• Logo (attached) - use of the same colour scheme

```html
<!DOCTYPE html>
<html lang="en">
<head>
<meta charset="utf-8">
<title>Nuvara Business Card</title>
<link href="https://fonts.googleapis.com/css2?family=Montserrat:wght@600;700&family=Raleway:wght@400;500&display=swap" rel="stylesheet">
<style>
  :root {
    --page-bg: #d9d6d2;
    --card-bg: #111111;
    --brand-blue: #1e9ad6;
    --brand-grey: #5c5c5c;
    --brand-yellow: #f2d21b;
    --text-light: #f2f2f2;
    --text-muted: #bdbdbd;
  }
  * { box-sizing: border-box; margin: 0; padding: 0; }
  html, body {
    width: 1200px; height: 960px; overflow: hidden;
    background: var(--page-bg);
  }
  .canvas {
    width: 1200px; height: 960px;
    display: flex; flex-direction: column; align-items: center; justify-content: center;
    gap: 30px;
  }
  .card {
    position: relative;
    width: 770px; height: 440px;
    background: var(--card-bg);
    box-shadow: 0 8px 24px rgba(0,0,0,0.25);
    overflow: hidden;
  }
  .rule {
    position: absolute; left: 0; right: 0; height: 3px;
    background: var(--brand-blue);
  }
  /* Front */
  .front .rule--top { top: 34px; }
  .front .rule--bottom { bottom: 120px; }
  .front .rule--base { bottom: 30px; }
  .brand {
    display: flex; align-items: center; gap: 22px;
  }
  .brand__mark {
    border-radius: 50%; border: 6px solid var(--brand-blue);
  }
  .brand__name {
    font-family: "Montserrat", sans-serif; font-weight: 700;
    color: var(--brand-grey); letter-spacing: 1px; line-height: 1;
  }
  .front .brand {
    position: absolute; top: 110px; left: 0; right: 0; justify-content: center;
  }
  .front .brand__mark { width: 92px; height: 92px; }
  .front .brand__name { font-size: 100px; }
  .front__web {
    position: absolute; bottom: 60px; left: 0; right: 0;
    display: flex; align-items: center; justify-content: center; gap: 12px;
    font-family: "Raleway", sans-serif; font-size: 20px; letter-spacing: 2px;
    color: var(--text-light);
  }
  /* Back */
  .back .rule--bottom { bottom: 70px; }
  .back .rule--top { top: 20px; }
  .back .brand { position: absolute; top: 56px; left: 64px; gap: 14px; }
  .back .brand__mark { width: 50px; height: 50px; border-width: 4px; }
  .back .brand__name { font-size: 62px; }
  .person {
    position: absolute; top: 150px; left: 64px;
    display: flex; align-items: center; gap: 14px;
  }
  .icon-ring {
    display: flex; align-items: center; justify-content: center;
    border: 3px solid var(--brand-blue); border-radius: 50%;
  }
  .person .icon-ring { width: 44px; height: 44px; }
  .person__name {
    font-family: "Raleway", sans-serif; font-weight: 500; font-size: 24px;
    letter-spacing: 1px; color: var(--brand-grey); line-height: 1.05;
  }
  .person__surname { color: var(--brand-blue); }
  .person__title {
    font-family: "Raleway", sans-serif; font-size: 16px; color: var(--text-muted);
  }
  .contacts {
    position: absolute; right: 56px; bottom: 110px;
    list-style: none; display: flex; flex-direction: column; gap: 12px;
    font-family: "Raleway", sans-serif; font-size: 18px; color: var(--text-light);
  }
  .contacts li { display: flex; align-items: center; justify-content: flex-end; gap: 16px; }
  .contacts .icon-ring { width: 36px; height: 36px; border-width: 2px; }
</style>
</head>
<body>
<main class="canvas">

  <section class="card front" aria-label="Card front">
    <div class="rule rule--top"></div>
    <div class="brand">
      <span class="brand__mark"></span>
      <span class="brand__name">Nuvara</span>
    </div>
    <div class="rule rule--bottom"></div>
    <p class="front__web">
      <svg width="16" height="16" viewBox="0 0 24 24" aria-hidden="true"><circle cx="12" cy="12" r="10" fill="none" stroke="#f2f2f2" stroke-width="2"/><path d="M2 12h20M12 2c3 3 3 17 0 20M12 2c-3 3-3 17 0 20" fill="none" stroke="#f2f2f2" stroke-width="1.6"/></svg>
      www.nuvara.com
    </p>
    <div class="rule rule--base"></div>
  </section>

  <section class="card back" aria-label="Card back">
    <div class="rule rule--top"></div>
    <div class="brand">
      <span class="brand__mark"></span>
      <span class="brand__name">Nuvara</span>
    </div>
    <div class="person">
      <span class="icon-ring">
        <svg width="22" height="22" viewBox="0 0 24 24" aria-hidden="true"><circle cx="12" cy="8" r="4.5" fill="#f2f2f2"/><path d="M3.5 22c0-5 3.8-8 8.5-8s8.5 3 8.5 8z" fill="#f2f2f2"/></svg>
      </span>
      <div>
        <p class="person__name">DANIEL <span class="person__surname">HAYES</span></p>
        <p class="person__title">Sales Director</p>
      </div>
    </div>
    <ul class="contacts">
      <li>daniel@nuvara.com
        <span class="icon-ring"><svg width="18" height="18" viewBox="0 0 24 24" aria-hidden="true"><rect x="2" y="5" width="20" height="14" rx="2" fill="#f2f2f2"/><path d="M2.5 6l9.5 7 9.5-7" fill="none" stroke="#111" stroke-width="2"/></svg></span>
      </li>
      <li>www.nuvara.com
        <span class="icon-ring"><svg width="18" height="18" viewBox="0 0 24 24" aria-hidden="true"><circle cx="12" cy="12" r="10" fill="none" stroke="#f2f2f2" stroke-width="2"/><path d="M2 12h20M12 2c3 3 3 17 0 20M12 2c-3 3-3 17 0 20" fill="none" stroke="#f2f2f2" stroke-width="1.6"/></svg></span>
      </li>
      <li>555-014-2871
        <span class="icon-ring"><svg width="16" height="16" viewBox="0 0 24 24" aria-hidden="true"><path d="M6.6 10.8a15 15 0 0 0 6.6 6.6l2.2-2.2a1 1 0 0 1 1-.25 11.4 11.4 0 0 0 3.6.57 1 1 0 0 1 1 1V20a1 1 0 0 1-1 1A17 17 0 0 1 3 4a1 1 0 0 1 1-1h3.5a1 1 0 0 1 1 1c0 1.25.2 2.45.57 3.57a1 1 0 0 1-.25 1z" fill="#f2f2f2"/></svg></span>
      </li>
    </ul>
    <div class="rule rule--bottom"></div>
  </section>

</main>
</body>
</html>
```